Business card design Needed for new logo / Construction business, home extensions and new builds

We need a business card design using our new logo files which i will attach to this project :)

We are a small construction business specialising in home extensions, new builds and property development. We are very ambitious and would appreciate professional and elegant designs for our new business card.

Very serious about using the services on MakerQuarry and recently acquired our new logo from here :)

Please get involved, i will feedback when i can as i am very busy but can respond daily, thanks

Target Market(s)

People that want to build onto their houses, new building developments or adding too their existing property

Industry/Entity Type

Construction

Contact Information for Business Card

Renwick Tolliver Construction, Lionel Ashby (Managing Director), Tel 07822254961, email - info@renwick-tolliver, www.renwick-tolliver.co.uk

Colors

Designer to choose colors to be used in the design.

Requirements
Must have
• I like a deep grey on the back please. A lot of you have provided black from and back, try mixing things up a little. The black looks cool 😎 Thanks

```html
<!DOCTYPE html>
<html lang="en">
<head>
<meta charset="utf-8">
<title>Renwick Tolliver Construction – Business Card</title>
<link rel="stylesheet" href="https://fonts.googleapis.com/css2?family=Open+Sans:wght@400;600;700&display=swap">
<style>
  :root {
    --stage: #232323;
    --card: #1e1e21;
    --card-edge: #141416;
    --gold: #e0a528;
    --gold-light: #f6d27a;
    --gold-dark: #a8741a;
    --silver: #d9dadc;
    --silver-light: #f7f7f8;
    --silver-dark: #8e9094;
    --ink: #f2f2f2;
  }
  * { box-sizing: border-box; margin: 0; padding: 0; }
  html, body {
    width: 1200px; height: 780px; overflow: hidden;
    background: var(--stage);
    font-family: "Open Sans", Arial, sans-serif;
  }
  .canvas {
    position: relative; width: 1200px; height: 780px;
    display: flex; align-items: center; justify-content: center; gap: 40px;
  }
  .card {
    position: relative; width: 560px; height: 320px;
    background: var(--card);
    border-radius: 18px; overflow: hidden;
    box-shadow: 0 14px 30px rgba(0,0,0,.55);
  }
  .card-band { position: absolute; left: 0; bottom: 0; width: 100%; height: 34px; }

  .brand {
    position: absolute; display: flex; align-items: center; gap: 10px;
    color: var(--gold); font-weight: 600; letter-spacing: .06em;
    text-transform: uppercase;
  }
  .brand-mark { width: 14px; height: 14px; background: var(--gold); flex: none; }
  .card-front .brand {
    left: 0; right: 0; top: 118px; justify-content: center; font-size: 21px;
  }
  .card-back .brand {
    left: 26px; top: 110px; font-size: 14px; width: 210px; line-height: 1.35;
  }

  .divider {
    position: absolute; left: 262px; top: 40px; width: 1px; height: 170px;
    background: linear-gradient(var(--silver-dark), var(--silver-light), var(--silver-dark));
  }
  .contact { position: absolute; left: 290px; top: 48px; color: var(--ink); }
  .contact-name { font-size: 26px; font-weight: 700; line-height: 1.1; color: var(--silver); }
  .contact-name .surname { color: var(--gold); }
  .contact-role { font-size: 13px; font-weight: 600; margin-top: 4px; }
  .contact-list { list-style: none; margin-top: 26px; font-size: 13px; }
  .contact-list li { display: flex; align-items: center; gap: 9px; line-height: 22px; }
  .contact-list svg { width: 13px; height: 13px; flex: none; }
  .address {
    position: absolute; left: 0; right: 0; bottom: 54px; text-align: center;
    color: var(--ink); font-size: 14px; letter-spacing: .02em;
  }
</style>
</head>
<body>
<main class="canvas">

  <section class="card card-front" aria-label="Card front">
    <div class="brand"><span class="brand-mark"></span>Renwick Tolliver Construction</div>
    <svg class="card-band" viewBox="0 0 560 34" preserveAspectRatio="none" aria-hidden="true">
      <defs>
        <linearGradient id="gold-front" x1="0" y1="0" x2="0" y2="1">
          <stop offset="0" stop-color="#f6d27a"/><stop offset=".5" stop-color="#e0a528"/><stop offset="1" stop-color="#a8741a"/>
        </linearGradient>
        <linearGradient id="silver-front" x1="0" y1="0" x2="0" y2="1">
          <stop offset="0" stop-color="#f7f7f8"/><stop offset=".5" stop-color="#c9cacd"/><stop offset="1" stop-color="#8e9094"/>
        </linearGradient>
      </defs>
      <polygon points="0,20 330,20 346,34 0,34" fill="url(#gold-front)"/>
      <polygon points="322,6 560,6 560,22 338,22" fill="url(#silver-front)"/>
    </svg>
  </section>

  <section class="card card-back" aria-label="Card back">
    <div class="brand"><span class="brand-mark"></span>Renwick Tolliver Construction</div>
    <div class="divider"></div>
    <div class="contact">
      <p class="contact-name">Lionel <span class="surname">Ashby</span></p>
      <p class="contact-role">Managing Director</p>
      <ul class="contact-list">
        <li>
          <svg viewBox="0 0 16 16" aria-hidden="true"><path fill="var(--gold)" d="M3.6 1.5 6 4.2 4.8 5.9c.8 1.8 2.4 3.4 4.3 4.3l1.7-1.2 2.7 2.4-1.4 2.4C6.8 13.4 2.6 9.2 1.2 3z"/></svg>
          07822 254 961
        </li>
        <li>
          <svg viewBox="0 0 16 16" aria-hidden="true"><rect x="1" y="3" width="14" height="10" rx="1" fill="var(--gold)"/><path d="M1.5 4 8 9l6.5-5" fill="none" stroke="var(--card)" stroke-width="1.3"/></svg>
          info@renwick-tolliver.co.uk
        </li>
        <li>
          <svg viewBox="0 0 16 16" aria-hidden="true"><circle cx="8" cy="8" r="6.5" fill="none" stroke="var(--gold)" stroke-width="1.5"/><path d="M1.5 8h13M8 1.5c-3 3.5-3 9.5 0 13M8 1.5c3 3.5 3 9.5 0 13" fill="none" stroke="var(--gold)" stroke-width="1.2"/></svg>
          www.renwick-tolliver.co.uk
        </li>
      </ul>
    </div>
    <p class="address">Kestrel Lane, Ashdown Vale, BH7 2QT</p>
    <svg class="card-band" viewBox="0 0 560 34" preserveAspectRatio="none" aria-hidden="true">
      <defs>
        <linearGradient id="gold-back" x1="0" y1="0" x2="0" y2="1">
          <stop offset="0" stop-color="#f6d27a"/><stop offset=".5" stop-color="#e0a528"/><stop offset="1" stop-color="#a8741a"/>
        </linearGradient>
        <linearGradient id="silver-back" x1="0" y1="0" x2="0" y2="1">
          <stop offset="0" stop-color="#f7f7f8"/><stop offset=".5" stop-color="#c9cacd"/><stop offset="1" stop-color="#8e9094"/>
        </linearGradient>
      </defs>
      <polygon points="0,20 330,20 346,34 0,34" fill="url(#gold-back)"/>
      <polygon points="322,6 560,6 560,22 338,22" fill="url(#silver-back)"/>
    </svg>
  </section>

</main>
</body>
</html>
```